Mastering Modern Vineyard Management

size of the ad - 8”x 10.75" plus 0.25" bleed
I would like an ad for a magazine that will stand out and make people want to read the ad.
The ad should not be crowded and people reading the ad will be able to read the text.
I would like it to be a creative and modern-day design.
the list of topics should not be the focus of the ad.
the text is attached.
If you decide to use people in the ad then please no ladies.
please note that leave over 1 inch for the bottom of the footer

```html
<!DOCTYPE html>
<html lang="en">
<head>
<meta charset="utf-8">
<title>Mastering Modern Vineyard Management – Course Ad</title>
<link rel="stylesheet" href="https://fonts.googleapis.com/css2?family=Anton&family=Barlow+Condensed:wght@500;600;700;800&family=Oswald:wght@300;400&family=Montserrat:wght@500;600;700;800&display=swap">
<style>
  :root {
    --navy: #0d3461;
    --navy-deep: #0a2a50;
    --blue: #1b6ec2;
    --yellow: #f2dc00;
    --red: #e0421b;
    --band-grey: #e9e8ef;
    --paper: #ffffff;
    --page-bg: #dcdcdf;
    --ink-white: #ffffff;
  }
  * { box-sizing: border-box; margin: 0; padding: 0; }
  html, body {
    width: 1200px; height: 800px; overflow: hidden;
    background: var(--page-bg);
  }
  .canvas {
    width: 1200px; height: 800px;
    display: flex; align-items: center; justify-content: center;
  }
  .ad {
    position: relative;
    width: 580px; height: 780px;
    background: var(--paper);
    overflow: hidden;
    box-shadow: 0 2px 10px rgba(0,0,0,.12);
  }
  .hero {
    position: absolute; left: 0; top: 0; width: 100%; height: 380px;
    background: var(--navy);
    overflow: hidden;
  }
  .hero__title {
    position: absolute; left: 34px; top: 30px;
    font-family: "Anton", sans-serif;
    font-size: 54px; line-height: 1; letter-spacing: 1px;
    color: var(--yellow);
    white-space: nowrap;
  }
  .hero__vineyard {
    position: absolute; left: 60px; top: 120px; width: 470px; height: 260px;
    background: linear-gradient(180deg, #e9edf5 0%, #c9d3e3 55%, #8a9ab5 100%);
    clip-path: polygon(0 40%, 14% 28%, 30% 20%, 46% 10%, 60% 6%, 74% 14%, 88% 24%, 100% 32%, 100% 100%, 0 100%);
  }
  .title-band {
    position: absolute; left: 0; top: 380px; width: 100%; height: 80px;
    background: var(--band-grey);
    padding: 10px 30px 0;
  }
  .title-band__course {
    font-family: "Barlow Condensed", sans-serif; font-weight: 800;
    font-size: 30px; line-height: 1.05; letter-spacing: .3px;
    color: var(--blue); text-transform: uppercase;
    white-space: nowrap;
  }
  .title-band__tagline {
    margin-top: 4px;
    font-family: "Barlow Condensed", sans-serif; font-weight: 500;
    font-size: 20px; letter-spacing: 1px;
    color: var(--navy); text-transform: uppercase;
    white-space: nowrap;
  }
  .info-band {
    position: absolute; left: 0; top: 460px; width: 100%; height: 78px;
    background: var(--navy-deep);
    display: flex; align-items: center;
    padding: 0 22px;
  }
  .info-band__divider {
    width: 1px; height: 50px; background: rgba(255,255,255,.45);
    margin: 0 15px; flex: 0 0 1px;
  }
  .info-band__location {
    font-family: "Oswald", sans-serif; font-weight: 300;
    font-size: 42px; line-height: 1; color: var(--yellow);
    text-transform: uppercase; white-space: nowrap;
  }
  .sessions { display: flex; align-items: center; color: var(--ink-white); white-space: nowrap; }
  .sessions__count {
    font-family: "Oswald", sans-serif; font-weight: 300;
    font-size: 48px; line-height: 1; margin-right: 6px;
  }
  .sessions__day {
    font-family: "Oswald", sans-serif; font-weight: 300;
    font-size: 28px; line-height: 1; text-transform: uppercase;
  }
  .sessions__label {
    font-family: "Montserrat", sans-serif; font-weight: 700;
    font-size: 9.5px; letter-spacing: .3px; text-transform: uppercase;
  }
  .start { white-space: nowrap; }
  .start__date {
    font-family: "Oswald", sans-serif; font-weight: 300;
    font-size: 21px; line-height: 1.1; color: var(--yellow);
    text-transform: uppercase;
  }
  .start__offer {
    font-family: "Montserrat", sans-serif; font-weight: 800;
    font-size: 12.5px; color: var(--ink-white); text-transform: uppercase;
  }
  .details {
    position: absolute; left: 0; top: 538px; width: 100%; height: 166px;
    padding: 12px 30px 0;
    text-align: center;
  }
  .details__scholarship {
    font-family: "Montserrat", sans-serif; font-weight: 800;
    font-size: 18px; color: var(--red); text-transform: uppercase;
  }
  .details__audience {
    margin-top: 2px;
    font-family: "Montserrat", sans-serif; font-weight: 700;
    font-size: 16px; color: var(--navy); white-space: nowrap;
  }
  .details__audience .accent { color: var(--blue); }
  .topics {
    position: relative; margin: 12px 6px 0;
    border: 1.5px solid var(--blue); border-radius: 8px;
    height: 96px;
    padding: 24px 16px 0;
    display: grid; grid-template-columns: 1.1fr 1.1fr 1fr; gap: 10px;
    text-align: left;
  }
  .topics__tab {
    position: absolute; left: 50%; top: -1px; transform: translateX(-50%);
    background: var(--blue); color: var(--ink-white);
    font-family: "Montserrat", sans-serif; font-weight: 700;
    font-size: 11px; letter-spacing: .3px; text-transform: uppercase;
    padding: 4px 18px; border-radius: 0 0 8px 8px;
    white-space: nowrap;
  }
  .topics__list { list-style: none; }
  .topics__item {
    display: flex; gap: 5px; align-items: flex-start;
    font-family: "Montserrat", sans-serif; font-weight: 500;
    font-size: 10.5px; line-height: 1.3; color: var(--navy);
    margin-bottom: 4px;
  }
  .topics__tick { flex: 0 0 10px; margin-top: 2px; }
  .footer-space {
    position: absolute; left: 0; bottom: 0; width: 100%; height: 76px;
    background: var(--paper);
  }
</style>
</head>
<body>
<main class="canvas">
  <article class="ad">
    <section class="hero">
      <h1 class="hero__title">VINEYARD COURSE</h1>
      <div class="hero__vineyard" role="img" aria-label="Illustration of pale rolling vineyard hills with rows of vines on navy"></div>
    </section>

    <section class="title-band">
      <h2 class="title-band__course">Mastering Modern Vineyard Management</h2>
      <p class="title-band__tagline">Investing in knowledge is investing in opportunities</p>
    </section>

    <section class="info-band">
      <div class="info-band__location">Brookvale</div>
      <span class="info-band__divider"></span>
      <div class="sessions">
        <span class="sessions__count">10</span>
        <div>
          <div class="sessions__day">Tuesday</div>
          <div class="sessions__label">Evenings sessions</div>
        </div>
      </div>
      <span class="info-band__divider"></span>
      <div class="start">
        <div class="start__date">Starting Feb.28</div>
        <div class="start__offer">Early bird special</div>
      </div>
    </section>

    <section class="details">
      <p class="details__scholarship">Limited partial scholarships</p>
      <p class="details__audience">For those that started <span class="accent">or</span> would like to go into viticulture</p>

      <div class="topics">
        <div class="topics__tab">Topics: partial listing</div>
        <ul class="topics__list">
          <li class="topics__item"><svg class="topics__tick" viewBox="0 0 10 10" aria-hidden="true"><circle cx="5" cy="5" r="5" fill="#1b6ec2"/><path d="M2.6 5.2l1.6 1.6 3.2-3.4" stroke="#fff" stroke-width="1.3" fill="none"/></svg>Vineyard investment strategies</li>
          <li class="topics__item"><svg class="topics__tick" viewBox="0 0 10 10" aria-hidden="true"><circle cx="5" cy="5" r="5" fill="#1b6ec2"/><path d="M2.6 5.2l1.6 1.6 3.2-3.4" stroke="#fff" stroke-width="1.3" fill="none"/></svg>Site selection</li>
          <li class="topics__item"><svg class="topics__tick" viewBox="0 0 10 10" aria-hidden="true"><circle cx="5" cy="5" r="5" fill="#1b6ec2"/><path d="M2.6 5.2l1.6 1.6 3.2-3.4" stroke="#fff" stroke-width="1.3" fill="none"/></svg>Financing</li>
        </ul>
        <ul class="topics__list">
          <li class="topics__item"><svg class="topics__tick" viewBox="0 0 10 10" aria-hidden="true"><circle cx="5" cy="5" r="5" fill="#1b6ec2"/><path d="M2.6 5.2l1.6 1.6 3.2-3.4" stroke="#fff" stroke-width="1.3" fill="none"/></svg>Canopy management</li>
          <li class="topics__item"><svg class="topics__tick" viewBox="0 0 10 10" aria-hidden="true"><circle cx="5" cy="5" r="5" fill="#1b6ec2"/><path d="M2.6 5.2l1.6 1.6 3.2-3.4" stroke="#fff" stroke-width="1.3" fill="none"/></svg>Irrigation planning</li>
          <li class="topics__item"><svg class="topics__tick" viewBox="0 0 10 10" aria-hidden="true"><circle cx="5" cy="5" r="5" fill="#1b6ec2"/><path d="M2.6 5.2l1.6 1.6 3.2-3.4" stroke="#fff" stroke-width="1.3" fill="none"/></svg>Vineyard legal basics</li>
          <li class="topics__item"><svg class="topics__tick" viewBox="0 0 10 10" aria-hidden="true"><circle cx="5" cy="5" r="5" fill="#1b6ec2"/><path d="M2.6 5.2l1.6 1.6 3.2-3.4" stroke="#fff" stroke-width="1.3" fill="none"/></svg>Sourcing buyers</li>
        </ul>
        <ul class="topics__list">
          <li class="topics__item"><svg class="topics__tick" viewBox="0 0 10 10" aria-hidden="true"><circle cx="5" cy="5" r="5" fill="#1b6ec2"/><path d="M2.6 5.2l1.6 1.6 3.2-3.4" stroke="#fff" stroke-width="1.3" fill="none"/></svg>Harvest logistics</li>
          <li class="topics__item"><svg class="topics__tick" viewBox="0 0 10 10" aria-hidden="true"><circle cx="5" cy="5" r="5" fill="#1b6ec2"/><path d="M2.6 5.2l1.6 1.6 3.2-3.4" stroke="#fff" stroke-width="1.3" fill="none"/></svg>Dealing with wineries</li>
          <li class="topics__item"><svg class="topics__tick" viewBox="0 0 10 10" aria-hidden="true"><circle cx="5" cy="5" r="5" fill="#1b6ec2"/><path d="M2.6 5.2l1.6 1.6 3.2-3.4" stroke="#fff" stroke-width="1.3" fill="none"/></svg>Tax fundamentals</li>
        </ul>
      </div>
    </section>

    <div class="footer-space" aria-hidden="true"></div>
  </article>
</main>
</body>
</html>
```